Upmarket Dessert Lounge needs a Business Card Design

We are an upmarket dessert lounge needing a business card to match our image.

We want something that is simple yet beautiful, feminine, classy, sophisticated and elegant. We want it to stand out and don't mind if it is bold.

The design should include our logo and colours of red or maroon with gold highlights. We don't mind if black is used.

Marlow & Quince

Target Market(s)

For those who like to indulge or treat themselves and give in to their temptations on good quality desserts.

Industry/Entity Type

Business

Requirements
Must have
• Must include our logo and our name

Marlow & Quince

M & Q

```html
<!DOCTYPE html>
<html lang="en">
<head>
<meta charset="utf-8">
<title>Marlow &amp; Quince — Business Card</title>
<link rel="stylesheet" href="https://fonts.googleapis.com/css2?family=Open+Sans:wght@400;600;700&display=swap">
<style>
  :root {
    --page-bg: #cfcfcf;
    --card-center: #4a4a4a;
    --card-edge: #050505;
    --maroon: #7a1316;
    --cream: #f6d0a0;
    --gold: #efc285;
    --ink-light: #ffffff;
  }
  * { margin: 0; padding: 0; box-sizing: border-box; }
  html, body {
    width: 956px;
    height: 1200px;
    overflow: hidden;
    background: var(--page-bg);
    font-family: "Open Sans", sans-serif;
  }
  .sheet { position: relative; width: 956px; height: 1200px; }
  .card {
    position: absolute;
    width: 798px;
    height: 456px;
    border-radius: 28px;
    overflow: hidden;
    background: radial-gradient(ellipse 60% 65% at 50% 50%, var(--card-center), var(--card-edge));
  }
  .card--front { left: 80px; top: 103px; }
  .card--back { left: 73px; top: 638px; }
  .card__swoosh { position: absolute; inset: 0; width: 100%; height: 100%; }
  .brand {
    position: absolute;
    left: 0; right: 0;
    text-align: center;
    color: var(--gold);
    font-weight: 600;
    white-space: nowrap;
  }
  .brand--initials { top: 95px; font-size: 72px; line-height: 84px; }
  .brand--name { top: 188px; font-size: 54px; line-height: 80px; letter-spacing: 1px; }
  .line {
    position: absolute;
    left: 0; right: 0;
    text-align: center;
    color: var(--ink-light);
    font-size: 19px;
    line-height: 24px;
    white-space: nowrap;
  }
  .line b { font-weight: 700; }
  .person { top: 264px; font-size: 21px; line-height: 26px; color: var(--gold); }
  .person b { font-weight: 700; }
  .contact--phones { top: 320px; }
  .contact--web { top: 355px; }
  .contact--address { top: 394px; }
</style>
</head>
<body>
<main class="sheet">
  <section class="card card--front" aria-label="Card front">
    <svg class="card__swoosh" viewBox="0 0 798 456" aria-hidden="true">
      <path d="M560 0 C650 5 740 22 798 56 L798 0 Z" fill="var(--maroon)"/>
      <path d="M630 12 Q740 28 798 80" fill="none" stroke="var(--cream)" stroke-width="6"/>
      <path d="M0 402 C80 432 170 450 250 456 L0 456 Z" fill="var(--maroon)"/>
      <path d="M0 382 Q80 422 165 444" fill="none" stroke="var(--cream)" stroke-width="6"/>
    </svg>
    <div class="brand brand--initials">M &amp; Q</div>
    <p class="line person"><b>Your Name -</b> Designation</p>
    <p class="line contact--phones"><b>p</b> : 123-456-7890 &nbsp;|&nbsp; <b>c</b> : 123-456-7890 &nbsp;|&nbsp; <b>f</b> : 123-456-7890</p>
    <p class="line contact--web"><b>e</b> : name@yourwebsite.com &nbsp;|&nbsp; <b>w</b> : www.marlowquince.com</p>
    <p class="line contact--address">0000, Street Name, City Name, Country Code.</p>
  </section>

  <section class="card card--back" aria-label="Card back">
    <div class="brand brand--name">MARLOW &amp; QUINCE</div>
  </section>
</main>
</body>
</html>
```